Electric mountain bike tours nz

We are an Electric Mountain bike tour company in New Zealand. We will be offering bike rental and guided tours around the Nelson region in New Zealand. I want our website to represent both Mountain biking and New Zealand with the colours layout and features. We want tabs for the following:
-1 about us
-2 what we offer
-3 bookings/contact
Under the about us tab will be who we are as a a company. I want the ability to add videos to each of these tabs as we move foward with videos of the tracks we will be riding. I want the website to be editable so I can add and remove videos/photos myself. Also "our bikes" will be under this tab.
Under the what we offer tab will be
-1 bike rental and pricing
-2 guided tours and pricing
-3 recommended package deals.
I want to able to put the tracks under the guided tours tab and select beginner/ intermediate/advanced and have the tracks in each of the following to match the rider level. Also to be able to have a small video of the track would be great in this section.
Bookings and contact tab
(Further information for this tab to be updated soon)
Coded - Design and coding required
1 page
- Silver ferns, kiwi, mountains

```html
<!DOCTYPE html>
<html lang="en">
<head>
<meta charset="utf-8">
<title>TRAILVOLT – Electric Bike Tours NZ</title>
<link href="https://fonts.googleapis.com/css2?family=Roboto+Condensed:ital,wght@0,700;1,700&family=Roboto:ital,wght@0,400;0,500;0,700;1,400&display=swap" rel="stylesheet">
<style>
:root{
  --green:#1f7a2e;
  --green-dark:#17621f;
  --orange:#f47a1f;
  --blue:#2751b5;
  --ink:#1c1c1c;
  --text:#555;
  --muted:#8a8a8a;
  --panel:#262626;
  --white:#fff;
  --line:#e2e2e2;
}
*{margin:0;padding:0;box-sizing:border-box}
html,body{width:1200px;height:4534px;overflow:hidden}
body{position:relative;background:var(--white);font-family:"Roboto",sans-serif;color:var(--text);font-size:14px}
.abs{position:absolute}
.head{font-family:"Roboto Condensed",sans-serif;font-weight:700;text-transform:uppercase;color:var(--ink)}
.btn{position:absolute;display:flex;align-items:center;justify-content:center;gap:8px;border-radius:30px;font-family:"Roboto",sans-serif;font-weight:700;font-size:15px;text-transform:uppercase;height:48px}
.btn-green{background:var(--green);color:var(--white)}
.btn-white{background:var(--white);color:var(--ink)}
.btn-outline{background:var(--white);color:var(--ink);border:2px solid var(--ink)}
.arrow-dot{width:16px;height:16px;border-radius:50%;background:currentColor;display:inline-flex;align-items:center;justify-content:center}
.arrow-dot svg{width:8px;height:8px}

.site-header{left:0;top:0;width:1200px;height:116px;background:var(--white)}
.logo{left:112px;top:10px;width:184px;height:184px;border-radius:50%;background:var(--white);border:3px solid var(--ink);z-index:5;display:flex;align-items:center;justify-content:center;font-weight:700;font-size:30px;color:var(--ink);letter-spacing:1px}
.nav{right:100px;top:62px;display:flex;gap:34px;font-size:15px;font-weight:700;color:var(--ink)}
.nav-home{position:relative}
.nav-home::before{content:"";position:absolute;left:50%;top:-30px;width:20px;height:20px;border-radius:50%;background:var(--ink);transform:translateX(-50%)}

.hero{left:0;top:116px;width:1200px;height:590px;background:linear-gradient(180deg,#6f8792 0%,#c9c0a8 35%,#4b4a36 62%,#23261c 100%)}
.hero-title{left:97px;top:320px;font-size:46px;color:var(--white);font-style:italic}
.hero-text{left:97px;top:396px;width:520px;font-size:19px;line-height:30px;color:var(--white)}
.hero-arrow{top:398px;color:var(--white);font-size:26px}

.ghost{font-family:"Roboto Condensed",sans-serif;font-weight:700;text-transform:uppercase;color:#f1f1f1;white-space:nowrap}
.section-title{font-size:36px;text-align:center;left:0;width:1200px}
.lede{left:290px;width:620px;text-align:center;font-size:13px;line-height:22px;color:var(--muted)}
.card{width:308px;height:294px;background:var(--white);box-shadow:0 2px 8px rgba(0,0,0,.22)}
.card .ph{height:214px;margin:8px}
.card p{padding:4px 22px;font-weight:700;font-size:17px;line-height:26px;color:#5a5a5a}

.split-title{font-size:30px;color:var(--white);font-style:italic}
.split-text{font-size:13px;line-height:22px;color:#e8e8e8;width:420px}

.tabs{left:0;width:1200px;top:1924px;display:flex;justify-content:center;gap:14px;font-size:13px;font-weight:500;color:var(--ink)}
.tabs span{padding:6px 12px}
.tabs .on{background:var(--ink);color:var(--white)}
.plan{background:var(--panel);color:var(--white);text-align:center}
.plan-top{display:flex;flex-direction:column;align-items:center;color:var(--white)}
.plan-name{height:56px;line-height:56px;font-size:28px;width:100%;font-style:italic}
.price{display:flex;align-items:flex-start;justify-content:center;padding-top:26px;font-weight:700}
.price .cur{font-size:26px;margin-top:6px}
.price .amt{font-size:68px;line-height:70px;margin:0 6px}
.price .per{font-size:14px;align-self:center;margin-top:26px;font-weight:400}
.plan-sub{font-family:"Roboto Condensed",sans-serif;font-style:italic;font-size:22px;text-transform:uppercase;padding:38px 0 26px;border-bottom:1px solid #3a3a3a;margin:0 20px}
.plan ul{list-style:none}
.plan li{font-size:14px;line-height:51px;border-bottom:1px solid #333;margin:0 30px;color:#ddd}
.plan .btn{position:relative;margin:20px auto 0;width:124px;height:42px;font-size:14px}

.banner{left:0;top:2820px;width:1200px;height:398px;background:linear-gradient(180deg,#46505a 0%,#5d6356 40%,#3a3d2c 75%,#2d2f24 100%)}
.banner-title{left:0;width:1200px;text-align:center;font-size:40px;line-height:52px;color:var(--white);font-style:italic;top:2926px}

.about-side{left:0;top:3640px;transform:rotate(-90deg);transform-origin:left top;font-size:96px;line-height:96px;color:#eeeeee;white-space:nowrap}
.about-title{left:100px;top:3302px;font-size:38px;font-style:italic}
.about-text{left:100px;width:525px;font-size:13px;line-height:22px;color:var(--text)}
.video-frame{left:720px;top:3312px;width:430px;height:268px;border:3px solid var(--green)}
.video{left:689px;top:3354px;width:408px;height:266px;background:linear-gradient(180deg,#3b4a2d,#6b7a43 45%,#a79263);box-shadow:0 2px 10px rgba(0,0,0,.3)}
.play{left:865px;top:3459px;width:56px;height:56px;border-radius:50%;background:rgba(255,255,255,.92);display:flex;align-items:center;justify-content:center;padding-left:4px}

.testi{width:300px;display:flex;gap:14px}
.avatar{width:64px;height:64px;border-radius:50%;background:linear-gradient(180deg,#8a6d5a,#4c3b31);flex:none;position:relative}
.avatar::after{content:"";position:absolute;left:23px;bottom:-8px;width:18px;height:18px;border-radius:50%;background:var(--green);border:2px solid var(--white)}
.stars{color:#f2b21b;font-size:15px;letter-spacing:1px}
.quote{font-size:13px;line-height:20px;font-style:italic;color:var(--muted);margin:4px 0 10px}
.t-name{font-weight:700;font-size:13px;color:var(--ink);text-transform:uppercase}
.t-role{font-size:12px;color:var(--muted)}
.dots{left:580px;top:4072px;display:flex;gap:6px}
.dots i{width:10px;height:10px;border-radius:50%;border:1px solid #777;display:block}
.dots i.on{background:#777}

.footer{left:0;top:4158px;width:1200px;height:376px;background:linear-gradient(180deg,#2b2b2b,#161616 40%)}
.foot-logo{left:120px;top:4230px;width:136px;height:136px;border-radius:50%;border:3px solid var(--white);display:flex;align-items:center;justify-content:center;font-weight:700;font-size:22px;color:var(--white)}
.social{left:100px;top:4388px;display:flex;gap:14px}
.social i{width:24px;height:24px;border-radius:50%;background:var(--white);display:block}
.foot-h{font-size:18px;color:var(--white);font-weight:500;text-transform:uppercase}
.foot-list{list-style:none;font-size:13px;color:#d5d5d5;line-height:29px}
.foot-list li::before{content:"›";color:var(--white);margin-right:10px;font-weight:700}
.email{left:828px;top:4318px;width:270px;height:34px;background:var(--white);font-size:13px;color:#999;padding:9px 14px}
.copy{left:0;width:1200px;top:4486px;text-align:center;font-size:14px;color:#d8d8d8}
.foot-rule{left:100px;top:4460px;width:1000px;height:1px;background:#3a3a3a}
</style>
</head>
<body>

<header class="abs site-header">
  <nav class="abs nav">
    <span class="nav-home">HOME</span><span>ABOUT US</span><span>WHAT WE OFFER</span><span>BOOKINGS</span><span>CONTACT US</span>
  </nav>
</header>
<div class="abs logo">TRAILVOLT</div>

<section class="abs hero" role="img" aria-label="Mountain biker resting with an electric bike on a hilltop bench at sunset over the coast"></section>
<h1 class="abs head hero-title">Electric Bike Tours</h1>
<p class="abs hero-text">Nemo enim ipsam voluptatem quia voluptas sit aspernatur aut odit aut fugit, sed quia consequuntur magni.</p>
<a class="btn btn-green" style="left:97px;top:485px;width:172px">Read More <span class="arrow-dot" style="color:#fff"><svg viewBox="0 0 8 8"><path d="M2 1l3 3-3 3" stroke="#1f7a2e" stroke-width="1.6" fill="none"/></svg></span></a>
<span class="abs hero-arrow" style="left:42px">‹</span>
<span class="abs hero-arrow" style="right:42px">›</span>

<div class="abs ghost" style="left:0;width:1200px;text-align:center;top:752px;font-size:78px">Welcome to TRAILVOLT</div>
<h2 class="abs head section-title" style="top:768px">Welcome to TRAILVOLT</h2>
<p class="abs lede" style="top:838px">At vero eos et accusamus et iusto odio dignissimos ducimus qui blanditiis praesentium voluptatum deleniti atque corrupti quos dolores et quas molestias excepturi sint occaecati cupiditate.</p>

<article class="abs card" style="left:100px;top:922px"><div class="ph" role="img" aria-label="Riders with mountain bikes beside a lake" style="background:linear-gradient(180deg,#5d7d8c,#8aa06a 55%,#51613a)"></div><p>The Summer Tours Feet Cycling City Name, NZ</p></article>
<article class="abs card" style="left:444px;top:922px"><div class="ph" role="img" aria-label="Electric mountain bike side view" style="background:linear-gradient(180deg,#eeeeee,#d6d6d6)"></div><p>The Summer Tours Feet Cycling City Name, NZ</p></article>
<article class="abs card" style="left:789px;top:922px"><div class="ph" role="img" aria-label="Group of cyclists riding on a grassy trail" style="background:linear-gradient(180deg,#7fa3c0,#6f9b4a 45%,#3e6a2a)"></div><p>The Summer Tours Feet Cycling City Name, NZ</p></article>

<a class="btn btn-green" style="left:404px;top:1266px;width:190px;font-size:14px">Book Your Bike</a>
<a class="btn btn-outline" style="left:607px;top:1266px;width:188px;font-size:14px">Download Guide</a>

<svg class="abs" style="left:0;top:1339px" width="1200" height="500" viewBox="0 0 1200 500">
  <defs>
    <linearGradient id="dk" x1="0" y1="0" x2="0" y2="1"><stop offset="0" stop-color="#4a4a44"/><stop offset="1" stop-color="#1f211c"/></linearGradient>
    <linearGradient id="gr" x1="0" y1="0" x2="0" y2="1"><stop offset="0" stop-color="#2d8a35"/><stop offset="1" stop-color="#1b6424"/></linearGradient>
  </defs>
  <polygon points="0,0 600,26 600,495 0,455" fill="url(#dk)" role="img" aria-label="Row of rental mountain bikes parked outside a shed"/>
  <polygon points="600,26 1200,0 1200,455 600,495" fill="url(#gr)" role="img" aria-label="Rider silhouetted on a trail, tinted green"/>
</svg>
<h3 class="abs head split-title" style="left:97px;top:1466px">Bike Rental</h3>
<p class="abs split-text" style="left:97px;top:1528px">At vero eos et accusamus et iusto odio dignissimos ducimus qui blan ditiis praesentium voluptatum deleniti atque corrupti quos dolores et quas molestias excepturi sint occaecati cupiditate non provident, similique sunt in culpa qui officia deserunt.</p>
<a class="btn btn-green" style="left:97px;top:1652px;width:148px;font-size:14px;height:44px">Book Now <span class="arrow-dot"><svg viewBox="0 0 8 8"><path d="M2 1l3 3-3 3" stroke="#1f7a2e" stroke-width="1.6" fill="none"/></svg></span></a>
<h3 class="abs head split-title" style="left:700px;top:1466px">Tours Guide</h3>
<p class="abs split-text" style="left:700px;top:1528px">At vero eos et accusamus et iusto odio dignissimos ducimus qui blan ditiis praesentium voluptatum deleniti atque corrupti quos dolores et quas molestias excepturi sint occaecati cupiditate non provident, similique sunt in culpa qui officia deserunt.</p>
<a class="btn btn-white" style="left:700px;top:1652px;width:148px;font-size:14px;height:44px">Download <span class="arrow-dot" style="color:#1c1c1c"><svg viewBox="0 0 8 8"><path d="M2 1l3 3-3 3" stroke="#fff" stroke-width="1.6" fill="none"/></svg></span></a>

<div class="abs ghost" style="left:0;width:1200px;text-align:center;top:1842px;font-size:78px">Our Packages</div>
<h2 class="abs head section-title" style="top:1858px">Our Packages</h2>
<div class="abs tabs"><span>BIKE RENTAL</span><span>GUIDED TOURS</span><span class="on">RECOMMENDED</span></div>

<div class="abs plan" style="left:100px;top:2040px;width:332px;height:613px">
  <div class="plan-top" style="background:var(--orange);height:188px">
    <div class="plan-name head" style="color:#fff;background:#e86f14">Starter</div>
    <div class="price"><span class="cur">$</span><span class="amt">19</span><span class="per">/ MONTH</span></div>
  </div>
  <div class="plan-sub">Single Place Travel</div>
  <ul><li>Lorem ipsum doloret</li><li>At vero eos et accusamus</li><li>Nam libero tempore coluta</li><li>Excepteur sint occaecat</li><li>On the other had esounce</li></ul>
  <a class="btn btn-green">Book Now</a>
</div>
<div class="abs plan" style="left:432px;top:2004px;width:333px;height:686px;z-index:2">
  <div class="plan-top" style="background:var(--green);height:224px">
    <div class="plan-name head" style="color:#fff;background:var(--green-dark)">Standard</div>
    <div class="price" style="padding-top:40px"><span class="cur">$</span><span class="amt">39</span><span class="per">/ MONTH</span></div>
  </div>
  <div class="plan-sub">Three Place Travel</div>
  <ul><li>Nam libero tempore coluta</li><li>On the other had esounce</li><li>Lorem ipsum doloret</li><li>At vero eos et accusamus</li><li>Excepteur sint occaecat</li></ul>
  <a class="btn btn-green">Book Now</a>
</div>
<div class="abs plan" style="left:765px;top:2040px;width:332px;height:613px">
  <div class="plan-top" style="background:var(--blue);height:188px">
    <div class="plan-name head" style="color:#fff;background:#1f45a3">Ultimate</div>
    <div class="price"><span class="cur">$</span><span class="amt">59</span><span class="per">/ MONTH</span></div>
  </div>
  <div class="plan-sub">Five Place Travel</div>
  <ul><li>Excepteur sint occaecat</li><li>Nam libero tempore coluta</li><li>At vero eos et accusamus</li><li>On the other had esounce</li><li>Lorem ipsum doloret</li></ul>
  <a class="btn btn-green">Book Now</a>
</div>

<section class="abs banner" role="img" aria-label="Orange electric mountain bike on a forest trail beside a road sign"></section>
<h2 class="abs head banner-title">Book Your Electric Bike Tours<br>in New Zealand</h2>
<a class="btn btn-green" style="left:522px;top:3060px;width:160px;height:44px;font-size:14px">Book Now <span class="arrow-dot" style="color:#fff"><svg viewBox="0 0 8 8"><path d="M2 1l3 3-3 3" stroke="#1f7a2e" stroke-width="1.6" fill="none"/></svg></span></a>

<div class="abs head about-side" style="color:#eee">About Us</div>
<h2 class="abs head about-title">Travel Further and Faster</h2>
<p class="abs about-text" style="top:3378px">Sed ut perspiciatis unde omnis iste natus error sit voluptatem accusantium doloremque lau dantium, totam rem aperiam, eaque ipsa quae ab illo.</p>
<p class="abs about-text" style="top:3444px">Inventore veritatis et quasi architecto beatae vitae dicta sunt explicabo. Nemo enim ipsam voluptatem quia voluptas sit aspernatur aut odit aut fugit, sed quia consequuntur magni dolores eos qui ratione voluptatem sequi nesciunt. Neque porro quisquam est, qui dolorem ipsum quia dolor sit amet, consectetur, adipisci velit.</p>
<a class="btn btn-green" style="left:100px;top:3576px;width:160px;height:46px;font-size:14px">Read More <span class="arrow-dot" style="color:#fff"><svg viewBox="0 0 8 8"><path d="M2 1l3 3-3 3" stroke="#1f7a2e" stroke-width="1.6" fill="none"/></svg></span></a>
<div class="abs video-frame"></div>
<div class="abs video" role="img" aria-label="Video still of an orange e-bike on a bush track"></div>
<div class="abs play"><svg width="18" height="20" viewBox="0 0 18 20"><polygon points="0,0 18,10 0,20" fill="#1f7a2e"/></svg></div>

<div class="abs" style="left:100px;top:3720px;width:1000px;height:1px;background:var(--line)"></div>
<h2 class="abs head section-title" style="top:3782px">Testimonials</h2>
<span class="abs" style="left:28px;top:3970px;font-size:26px;color:#777">‹</span>
<span class="abs" style="right:28px;top:3970px;font-size:26px;color:#777">›</span>

<div class="abs testi" style="left:100px;top:3862px">
  <div class="avatar" role="img" aria-label="Customer portrait"></div>
  <div><div class="stars">★★★★☆</div><p class="quote">" At vero eos et accusamus et iusto odio dignissimos ducimus qui blanditiis praesent ium voluptatum deleniti atque corrupti quos dolores quas molestias "</p><div class="t-name">Mara Kellow</div><div class="t-role">Creative Manager, NZ</div></div>
</div>
<div class="abs testi" style="left:444px;top:3862px">
  <div class="avatar" role="img" aria-label="Customer portrait"></div>
  <div><div class="stars">★★★★☆</div><p class="quote">" At vero eos et accusamus et iusto odio dignissimos ducimus qui blanditiis praesent ium voluptatum deleniti atque corrupti quos dolores quas molestias "</p><div class="t-name">Tane Harlow</div><div class="t-role">Events Manager, NZ</div></div>
</div>
<div class="abs testi" style="left:792px;top:3862px">
  <div class="avatar" role="img" aria-label="Customer portrait"></div>
  <div><div class="stars">★★★★☆</div><p class="quote">" At vero eos et accusamus et iusto odio dignissimos ducimus qui blanditiis praesent ium voluptatum deleniti atque corrupti quos dolores quas molestias "</p><div class="t-name">Rory Patane</div><div class="t-role">Sports Manager, NZ</div></div>
</div>
<div class="abs dots"><i></i><i class="on"></i><i></i></div>

<footer class="abs footer" role="img" aria-label="Dark mountain landscape at dusk"></footer>
<div class="abs foot-logo">TRAILVOLT</div>
<div class="abs social"><i></i><i></i><i></i><i></i><i></i></div>

<div class="abs foot-h" style="left:414px;top:4238px">Quick Links</div>
<ul class="abs foot-list" style="left:414px;top:4268px"><li>Home</li><li>About Us</li><li>What We Offer</li><li>Tour Guide</li><li>Contact Us</li></ul>
<ul class="abs foot-list" style="left:588px;top:4268px"><li>Info</li><li>Blog Post</li><li>Press</li><li>Privacy Policy</li><li>Terms of Service</li></ul>

<div class="abs foot-h" style="left:828px;top:4238px">Newsletter Subscription</div>
<p class="abs" style="left:828px;top:4272px;width:260px;font-size:13px;line-height:20px;color:#d5d5d5">Register your Email Address to get a more information about us</p>
<div class="abs email">Email</div>
<a class="btn btn-green" style="left:828px;top:4368px;width:102px;height:34px;font-size:13px">Subscribe</a>

<div class="abs foot-rule"></div>
<p class="abs copy">Copyrights © 2018 TRAILVOLT. All Rights Reserved.</p>

</body>
</html>
```